Systems and Technology Consultants - Website

Design & Build a website for a new company which operates in the Systems and Technology space for Transportation, Government and Commercial sectors.

Overall design should be minimalist in nature.
Should also have a feed that provides news and event updates on the main page.
Logo has already been awarded and should be incorporated into the site.

We like the overall layout, functionality and simplicity of the below sites. Submitted designs could be similar to or a combination of the aspects on these sites, or perhaps a whole different concept - we are open to new ideas.
Norvique.com
Teblo.it

Update 1 Dated 27 May 2014

All I am moving away from the Teblo.it website and would like it to be more aligned with Norvique.com not only in layout but in functionality. I will be extending the deadline of this design brief for two weeks to incorporate additional requirements and will add addtional funding to the project.

Apologies for not having more information available to provide but with so many submissions its getting confusing.

Thanks Derek

Please note that the brief has been updated and the deadline has been extended.

Important: We will need two language versions of the website, English and Arabic; the website is hosted on HostPelican

Hello All, Thank you for your submissions. We have narrowed it down to the final 6 designers and I just wanted to take a moment and provide a bit of feedback regarding the concepts that we like and the modifications we are looking for. First, let me mention some of the design functions we like. - At the top of the homepage we really like the "region" or "language" tab so that the website can be viewed in both English and Arabic. - We like the homepage to have clear color variation so that the different sections of the homepage are distinct. Additionally, we like the bottom portion of the homepage to be in red. We feel that draws attention to our contact information. Again, we would like the colors to integrate black, gray-scale, red, etc. - Having a search tab at the top of the home page, or integrated into the main image, so that the site is easy to navigate. - We especially like the main image to have the scrolling tabs at the bottom so it is easy to browse the services offered (Consultancy, Solutions Architecture, Masters Systems Integration, Independent Design Review). - In regards to the services offered tab we really like the idea that a few people presented that have the outside of our logo with an icon in the middle of consultancy, solutions, etc., etc. Secondly, as mentioned in our brief we really enjoy the design of norvique site. Specially, we enjoy the strong iconic images they use, the way the tabs at the top scroll easily, and contact us page that generates an email. Lastly, I've included some photos of the concept we have been working on. What we are trying to demonstrate is how our company offers a range of services that are essentially linked together. We provide individual services that when combined present the full service package. We would like this concept to be integrated into the over concept of our website. Please feel free to ask for clarification of any of the above points or contact us if you have any additional questions. We appreciate all of your hard work and are very excited to see the updated designs. Best, Marta Vennick Quelbrant Senior Program Manager marta.vennick@quelbrant-example.com

Industry/Entity Type

Government

Font styles to use
Serif
Sans Serif

Requirements
Must have
• Must work on/adapt to various/mobile devices (responsive)
Must be simple and straightforward
Colors should be in line/matching with logo
2 language versions: English and Arabic (no Thai)
Services should be the first group/row of items after/below the main image
Note: the website will be hosted by hostpelican
Nice to have
• Submit feedback form
What's New section
The banner at the bottom of the site should not be too large; we would like a narrow one more
It would be nice if the header/top banner (with Home, About, etc. tabs) could stay in place as you scroll down (like Norvique and Chatterloop)
We will likely only use one image with a Company slogan on the Home page rather than a carousel of images to rotate through
Should not have
• This is the existing website: http://www.quelbrant-example.org
We do not like the animation, the way the banner icons/titles bounce
Not simple enough, we don't like the functionality or how pages load so slowly
We do not like the logo centered - it should be at the left
The banner and its tabs should not be towards the right, we would like them to be centered, to go all the way across and to be below the logo

```html
<!DOCTYPE html>
<html lang="en">
<head>
<meta charset="utf-8">
<title>Quelbrant – Systems and Technology Consultants</title>
<link href="https://fonts.googleapis.com/css2?family=Raleway:wght@400;500;600;700&family=Open+Sans:wght@400;600&display=swap" rel="stylesheet">
<style>
:root{
  --red:#f5333f;
  --red-dark:#e02530;
  --ink:#1e1e1e;
  --header:#2b2b2b;
  --footer:#2e2e2e;
  --footer-base:#1f1f1f;
  --text:#333;
  --muted:#777;
  --light:#e6e6e6;
  --white:#fff;
}
*{margin:0;padding:0;box-sizing:border-box}
html,body{width:838px;height:1200px;overflow:hidden;background:var(--white)}
body{font-family:"Open Sans",Arial,sans-serif;color:var(--text)}
.page{position:relative;width:838px;height:1200px}
.abs{position:absolute}

/* Header */
.site-header{left:0;top:0;width:838px;height:90px;background:linear-gradient(#303030,#262626)}
.nav a{position:absolute;top:37px;font-size:10.5px;color:var(--white);text-decoration:none;letter-spacing:.2px}
.brand{left:369px;top:34px;width:100px;text-align:center;font-family:"Raleway",sans-serif;font-weight:700;font-size:15px;letter-spacing:1.5px;color:var(--red)}

/* Hero */
.hero{left:0;top:90px;width:838px;height:307px;background:linear-gradient(90deg,#c9c9c9 0%,#dadada 45%,#cfcfcf 100%)}
.hero-visual{left:400px;top:90px;width:438px;height:307px;background:radial-gradient(ellipse at 70% 40%,#eaeaea 0%,#c8c8c8 55%,#b8b8b8 100%)}
.hero-kicker{left:70px;top:165px;font-family:"Raleway",sans-serif;font-size:15px;font-weight:500;color:var(--ink);letter-spacing:.3px}
.hero-title{left:69px;top:182px;font-family:"Raleway",sans-serif;font-size:33px;font-weight:700;color:var(--ink);letter-spacing:.5px}
.hero-title span{color:var(--red)}
.hero-lead{left:70px;top:227px;width:380px;font-size:12px;line-height:15.5px;color:#444}
.btn{top:273px;width:122px;height:26px;font-family:"Raleway",sans-serif;font-size:12px;font-weight:500;color:var(--white);text-align:center;line-height:26px;border-radius:2px}
.btn-primary{left:70px;background:var(--red)}
.btn-dark{left:203px;background:var(--ink)}

/* Who we are */
.section-title{font-family:"Raleway",sans-serif;color:var(--ink)}
.who-title{left:0;width:838px;top:418px;text-align:center;font-size:22px;font-weight:500}
.who-text{left:125px;width:588px;top:453px;text-align:center;font-size:9px;line-height:15.5px;color:var(--muted)}

/* Services */
.services-title{left:70px;top:540px;font-size:16px;font-weight:500}
.service{top:586px;height:91px;background:var(--red);border:2px solid #ff7a82;text-align:center;color:var(--white)}
.service svg{position:absolute;left:50%;top:9px;margin-left:-22px}
.service-name{position:absolute;left:0;right:0;top:59px;font-family:"Raleway",sans-serif;font-size:13px;font-weight:600}
.service-tip{position:absolute;left:50%;bottom:-8px;margin-left:-6px;width:0;height:0;border-left:6px solid transparent;border-right:6px solid transparent}
.tip-down{border-top:6px solid #ff9aa0}
.tip-up{bottom:-2px;border-bottom:6px solid #ffb6ba}
.services-copy{left:70px;top:696px;width:698px;font-size:9px;line-height:15.5px;color:var(--muted)}
.services-copy strong{font-size:12.5px;font-weight:400;color:var(--ink)}

/* News & Testimonials */
.news-title{left:70px;top:806px;font-size:15px;font-weight:500}
.news-photo{left:70px;top:840px;width:85px;height:49px;background:linear-gradient(135deg,#5b6e86,#9aa7b6 55%,#d8d6d0)}
.person-name{font-family:"Raleway",sans-serif;font-size:8px;font-weight:700;color:var(--red)}
.person-role{font-size:7px;color:#555}
.news-meta{left:161px;top:841px}
.news-head{left:161px;top:867px;width:210px;font-size:9px;line-height:11.5px;color:var(--ink)}
.news-body{left:70px;top:895px;width:325px;font-size:8.8px;line-height:13.5px;color:var(--muted)}
.divider{left:407px;top:810px;width:2px;height:150px;background:linear-gradient(#fff,#e2e2e2 30%,#e2e2e2 70%,#fff)}
.testi-title{left:456px;top:806px;font-size:15px;font-weight:500}
.avatar{left:450px;top:844px;width:77px;height:77px;border-radius:50%;border:3px solid #eee;background:radial-gradient(circle at 50% 40%,#e2b99a,#b98a6c 60%,#8c6a55)}
.quote-mark{font-family:Georgia,serif;font-size:16px;color:#888}
.q-open{left:528px;top:839px}
.quote{left:542px;top:851px;width:226px;font-size:8.8px;line-height:14px;color:var(--muted)}
.q-close{left:610px;top:877px}
.testi-meta{left:541px;top:910px}
.dots{left:746px;top:946px}
.dots i{display:inline-block;width:6px;height:6px;border-radius:50%;background:#888;margin-right:1px}
.dots i.on{background:var(--red)}

/* Footer */
.site-footer{left:0;top:1004px;width:838px;height:172px;background:var(--footer)}
.footer-head{top:1023px;font-family:"Raleway",sans-serif;font-size:13.5px;font-weight:500;color:var(--white)}
.footer-text{font-size:9px;line-height:13px;color:#eee}
.footer-list{list-style:none;top:1053px;font-size:9px;line-height:15.4px;color:#ddd}
.newsletter{left:70px;top:1085px;width:185px;height:27px;background:var(--white);border:1px solid #ddd}
.newsletter span{position:absolute;left:7px;top:7px;font-size:8.5px;color:#999}
.newsletter svg{position:absolute;right:9px;top:5px}
.social{top:1125px;width:18px;height:18px;border-radius:50%;background:#8a8a8a}
.contact-row{left:620px;font-size:8.8px;line-height:12.5px;color:#eee}
.copyright{left:0;top:1176px;width:838px;height:24px;background:var(--footer-base);text-align:center;font-size:8px;line-height:24px;color:#ddd}
</style>
</head>
<body>
<div class="page">

  <header class="abs site-header">
    <nav class="nav">
      <a style="left:69px">HOME</a>
      <a style="left:127px">BUSINESS UNITS</a>
      <a style="left:233px">SERVICES</a>
      <a style="left:545px">ABOUT US</a>
      <a style="left:623px">LOCATIONS</a>
      <a style="left:706px">CONTACT US</a>
    </nav>
    <div class="abs brand">QUELBRANT</div>
  </header>

  <section class="abs hero"></section>
  <div class="abs hero-visual" role="img" aria-label="Businessman holding a tablet beside a line-drawn globe with world landmarks"></div>
  <p class="abs hero-kicker">WELCOME TO THE</p>
  <h1 class="abs hero-title">QUELBRANT <span>TECHNIK</span></h1>
  <p class="abs hero-lead">Sed ut perspiciatis unde omnis iste natus error sit et quasi beatae vitae dicta sunt explicabo nemo enim ipsam voluptatem quia</p>
  <a class="abs btn btn-primary">Read More</a>
  <a class="abs btn btn-dark">Free Trial Now</a>

  <h2 class="abs section-title who-title">Who we are</h2>
  <p class="abs who-text">quelbrant specializes in delivering quality professional services and technical projects that support larger business goals.&nbsp; systems are tools that support a greater business function and need. we understand that most technical projects are conceptualized to support a larger vision</p>

  <h2 class="abs section-title services-title">Services Offered</h2>

  <div class="abs service" style="left:70px;width:169px">
    <svg width="44" height="44" viewBox="0 0 44 44" fill="none" stroke="#fff" stroke-width="1.4"><circle cx="22" cy="22" r="20.5"/><circle cx="22" cy="18" r="4" fill="#fff"/><path d="M15 30c0-5 3-7 7-7s7 2 7 7z" fill="#fff"/></svg>
    <div class="service-name">Consulting</div>
    <span class="service-tip tip-down"></span>
  </div>
  <div class="abs service" style="left:244px;width:169px">
    <svg width="44" height="44" viewBox="0 0 44 44" fill="none" stroke="#fff" stroke-width="1.4"><circle cx="22" cy="22" r="20.5"/><circle cx="19" cy="20" r="4"/><circle cx="19" cy="20" r="1.4"/><path d="M24 24h7v6h-12v-3M14 30h17"/></svg>
    <div class="service-name">Engineering</div>
    <span class="service-tip tip-up"></span>
  </div>
  <div class="abs service" style="left:422px;width:170px">
    <svg width="44" height="44" viewBox="0 0 44 44" fill="none" stroke="#fff" stroke-width="1.4"><circle cx="22" cy="22" r="20.5"/><g stroke-width="1"><rect x="15" y="22" width="3" height="3"/><rect x="20" y="22" width="3" height="3"/><rect x="25" y="22" width="3" height="3"/><rect x="15" y="27" width="3" height="3"/><rect x="20" y="27" width="3" height="3"/><rect x="25" y="27" width="3" height="3"/><circle cx="22" cy="17" r="1.6"/><circle cx="28" cy="15" r="1.6"/></g></svg>
    <div class="service-name">Maintenance</div>
    <span class="service-tip tip-up"></span>
  </div>
  <div class="abs service" style="left:599px;width:169px">
    <svg width="44" height="44" viewBox="0 0 44 44" fill="none" stroke="#fff" stroke-width="1.4"><circle cx="22" cy="22" r="20.5"/><path d="M17 17a5 5 0 0 1 10 0z" fill="#fff"/><circle cx="22" cy="20" r="3.2" fill="#fff"/><path d="M15 31c0-5 3-7 7-7s7 2 7 7z" fill="#fff"/></svg>
    <div class="service-name">Construction</div>
    <span class="service-tip tip-up"></span>
  </div>

  <p class="abs services-copy"><strong>Sed ut perspiciatis unde omnis iste natus error sit</strong> voluptatem accusantium doloremque laudantium, totam rem aperiam, eaque ipsa quae ab illo inventore veritatis et quasi architecto beatae vitae dicta sunt explicabo. Nemo enim ipsam voluptatem quia voluptas sit aspernatur aut odit aut fugit, sed quia consequuntur magni dolores eos qui ratione voluptatem sequi nesciunt. Neque porro quisquam est, qui dolorem ipsum quia dolor sit amet, consectetur, adipisci velit, sed quia non numquam eius modi.</p>

  <h2 class="abs section-title news-title">Latestnews</h2>
  <div class="abs news-photo" role="img" aria-label="Business colleagues reviewing documents at a desk"></div>
  <div class="abs news-meta"><div class="person-name">Petter John</div><div class="person-role">SEO, Company Name</div></div>
  <p class="abs news-head">Sed ut perspiciatis unde omnis iste natus error sit unde omnis iste natus error sit</p>
  <p class="abs news-body">voluptatem accusantium doloremque laudantium, totam rem aperiam, eaque ipsa quae ab illo inventore veritatis et quasi architecto beatae vitae dicta sunt explicabo.</p>

  <div class="abs divider"></div>

  <h2 class="abs section-title testi-title">Testimonials</h2>
  <div class="abs avatar" role="img" aria-label="Portrait photo of the client giving the testimonial"></div>
  <span class="abs quote-mark q-open">&ldquo;</span>
  <p class="abs quote">It is a long established fact that a reader will be distracted by the readable content of a page when looking at its layout.</p>
  <span class="abs quote-mark" style="left:609px;top:878px">&rdquo;</span>
  <div class="abs testi-meta"><div class="person-name">Adam John</div><div class="person-role">SEO, Company Name</div></div>
  <div class="abs dots"><i class="on"></i><i></i><i></i></div>

  <footer class="abs site-footer"></footer>
  <h3 class="abs footer-head" style="left:70px">Newslatter</h3>
  <p class="abs footer-text" style="left:71px;top:1053px;width:190px">Lorem ipsum dolor sit amet elit, sed do ut labore et dolore magna aliqua Ut enim ad</p>
  <div class="abs newsletter">
    <span>Your email here</span>
    <svg width="17" height="17" viewBox="0 0 17 17" fill="none" stroke="#222" stroke-width="1.3"><circle cx="8.5" cy="8.5" r="7.5"/><path d="M4.5 8.5h7M8.5 5.5l3 3-3 3"/></svg>
  </div>
  <span class="abs social" style="left:70px"></span>
  <span class="abs social" style="left:94px"></span>
  <span class="abs social" style="left:117px"></span>
  <span class="abs social" style="left:140px"></span>
  <span class="abs social" style="left:163px"></span>
  <span class="abs social" style="left:186px"></span>

  <h3 class="abs footer-head" style="left:308px">Business Unit</h3>
  <ul class="abs footer-list" style="left:309px"><li>lorem ipsum</li><li>is simply dummy</li><li>text of the</li><li>prinnting</li><li>and typesrtting</li><li>industry</li></ul>

  <h3 class="abs footer-head" style="left:463px">Site Map</h3>
  <ul class="abs footer-list" style="left:463px"><li>lorem ipsum</li><li>is simply dummy</li><li>text of the</li><li>prinnting</li><li>and typesrtting</li><li>industry</li></ul>

  <h3 class="abs footer-head" style="left:624px">Contact Us</h3>
  <svg class="abs" style="left:598px;top:1053px" width="18" height="15" viewBox="0 0 18 15" fill="#ddd"><path d="M9 1 1 8h2v6h4v-4h4v4h4V8h2z"/></svg>
  <p class="abs contact-row" style="top:1054px;width:150px">Lorem ipsum dolor sit amet elit, sed do eiusmod tempor incididunt ut labore</p>
  <svg class="abs" style="left:604px;top:1096px" width="9" height="15" viewBox="0 0 9 15" fill="none" stroke="#ddd" stroke-width="1.3"><rect x="1" y="1" width="7" height="13" rx="1.2"/><path d="M3.5 11.5h2"/></svg>
  <p class="abs contact-row" style="top:1099px">(0800)410.552.786</p>
  <svg class="abs" style="left:596px;top:1123px" width="21" height="12" viewBox="0 0 21 12" fill="none" stroke="#ddd" stroke-width="1.2"><rect x="5" y="1" width="15" height="10"/><path d="M5 1l7.5 6L20 1M0 4h3M1 7h3"/></svg>
  <p class="abs contact-row" style="left:625px;top:1124px">info@companyname.com</p>

  <div class="abs copyright">Copyright © 2014 companyname.com - All Rights Reserved</div>
</div>
</body>
</html>
```